Creation of an elegant and modern turnkey Shopify website

Hello,

We are a new company specializing in the sale of above-ground pools. We want to create a turnkey website, ideally using Shopify. For now, we need a "showcase" site, not an e-commerce platform, with four tabs:

Home Page (an overall presentation of the company)
Our Products (an overview of all the above-ground pools we sell)
Our Projects (a page inspired by Instagram to showcase photos of our future projects)
Contact (a page with all our contact information and a contact form)

We are looking to create a highly visual, elegant, and modern website with vibrant splashes of color. We will provide the text, photos (along with instructions on where to place them on each page), and all other necessary information as attachments.

Thank you in advance for your proposals!

The Brisa Lagoon Team

Target Market(s)

Targeted at Swiss customers (a translator will need to be installed for different languages)

Industry/Entity Type

Sale of customised above-ground pools

Coding

Coded - Design and coding required

Font styles to use
Sans Serif

Colors
0094D4
00A9DD
6FCCEA
C7EBF8
E9F6FB
00AB8E
00BBA5
67D7C9
C6EFE9
E9F9F6

Requirements
Must have
• A stunning, elegant and modern look
Nice to have
• Inspiration from the colors of our logo throughout the site, but in an elegant way
Should not have
• An overly classic look for swimming pool sites

```html
<!DOCTYPE html>
<html lang="en">
<head>
<meta charset="utf-8">
<title>Brisa Lagoon – Premium Above-Ground Pools</title>
<link rel="stylesheet" href="https://fonts.googleapis.com/css2?family=Outfit:wght@300;400;500;600&display=swap">
<style>
:root{
  --aqua:#00dde6;
  --aqua-soft:#4fcfd9;
  --royal:#0a78f2;
  --ocean:#1a86ee;
  --sky:#19b6ef;
  --card-cyan:#06e2f0;
  --white:#ffffff;
  --ink:#1a2a3a;
}
*{margin:0;padding:0;box-sizing:border-box}
html,body{width:1200px;height:4277px;overflow:hidden}
body{position:relative;font-family:'Outfit',sans-serif;color:var(--white);background:var(--white)}
.abs{position:absolute}
.photo{position:absolute}
/* header */
.site-header{left:0;top:0;width:1200px;height:143px;background:var(--white)}
.brand{left:76px;top:34px;display:flex;align-items:center;gap:12px}
.brand-dot{width:26px;height:26px;border-radius:50%;background:var(--aqua)}
.brand-name{font-size:34px;font-weight:300;color:var(--ink);letter-spacing:1px}
.main-nav a{position:absolute;top:64px;font-size:13px;color:var(--ink);text-decoration:none}
.main-nav a.active::after{content:"";position:absolute;left:0;right:0;bottom:-10px;height:3px;background:var(--aqua);border-radius:2px}
.nav-cta{left:988px;top:56px;width:136px;height:40px;border-radius:20px;background:var(--aqua);font-size:13px;display:flex;align-items:center;justify-content:center}
/* buttons */
.btn-outline{position:absolute;display:flex;align-items:center;justify-content:center;gap:22px;border:1.5px solid var(--white);border-radius:32px;font-size:23px;font-weight:300}
.btn-outline .arrow{width:20px;height:20px}
/* headings */
.title{font-weight:300;line-height:1.2}
.rule{position:absolute;height:3px;width:76px;background:var(--white)}
.copy{font-size:13px;line-height:1.9;font-weight:300}
/* hero */
.hero-band{left:0;top:717px;width:1200px;height:329px;background:var(--aqua);text-align:center}
.hero-band h1{position:absolute;left:0;right:0;top:38px;font-size:56px}
.hero-band p{position:absolute;left:0;right:0;top:176px;font-size:21px;font-weight:300}
/* why */
.why-panel{left:614px;top:1055px;width:586px;height:695px;background:var(--royal)}
.why-panel h2{position:absolute;left:57px;top:100px;font-size:43px}
.why-list{position:absolute;left:64px;top:285px;width:440px;list-style:none}
.why-list li{position:relative;padding-left:59px;font-size:12.5px;line-height:1.75;font-weight:300}
.why-list li b{font-weight:500;font-size:14px}
.why-list svg{position:absolute;left:0;top:0;width:44px;height:44px}
/* personalized */
.service-panel{left:0;top:1759px;width:458px;height:536px;background:var(--aqua-soft)}
.service-panel h2{position:absolute;left:76px;top:66px;font-size:44px}
.service-panel .copy{position:absolute;left:74px;top:242px;width:348px}
/* products */
.products{left:0;top:2300px;width:1200px;height:685px;background:linear-gradient(180deg,#1b6fd6 0%,#1f82e6 40%,#2c9bf0 100%)}
.products h2{position:absolute;left:0;right:0;top:108px;text-align:center;font-size:44px}
.product-card{position:absolute;top:263px;width:254px;height:309px;background:var(--card-cyan)}
.product-card .pic{position:absolute;left:0;top:0;width:254px;height:231px}
.product-card .label{position:absolute;left:0;right:0;top:231px;height:78px;display:flex;align-items:center;justify-content:center;text-align:center;font-size:17px;font-weight:500;line-height:1.05;padding:0 14px}
.product-card.featured{background:rgba(40,200,235,.75);text-align:center}
.product-card.featured h3{margin-top:44px;font-size:18px;font-weight:500;line-height:1.15}
.product-card.featured .mini-rule{width:36px;height:2px;background:var(--white);margin:8px auto}
.product-card.featured p{font-size:12.5px;line-height:1.9;font-weight:300;padding:0 22px}
.product-card.featured .btn-outline{left:62px;top:242px;width:130px;height:36px;font-size:12px;gap:12px}
/* satisfaction */
.satisfaction{left:0;top:2993px;width:1200px;height:484px;background:radial-gradient(ellipse at 50% 50%,#1aa6de 0%,#1487c6 60%,#b8895e 100%);text-align:center}
.satisfaction h2{position:absolute;left:0;right:0;top:116px;font-size:45px}
.satisfaction .copy{position:absolute;left:0;right:0;top:236px}
.satisfaction .warranty{position:absolute;left:0;right:0;top:286px;font-size:21px;font-weight:400}
/* contact */
.contact-panel{left:661px;top:3487px;width:539px;height:479px;background:var(--aqua-soft)}
.contact-panel h2{position:absolute;left:41px;top:54px;font-size:45px}
.contact-panel .copy{position:absolute;left:41px;top:195px;width:400px}
/* footer */
.site-footer{left:0;top:3974px;width:1200px;height:240px;background:var(--ocean)}
.footer-item{position:absolute;top:80px;display:flex;gap:18px;align-items:center;font-size:13.5px;line-height:1.3}
.footer-item svg{width:30px;height:30px}
.footer-rule{position:absolute;left:80px;right:72px;top:162px;border-top:1px dashed rgba(255,255,255,.5)}
.footer-nav a{position:absolute;top:189px;font-size:12.5px;color:var(--white);text-decoration:none}
.footer-nav a.active{font-weight:600}
.footer-bar{left:0;top:4214px;width:1200px;height:63px;background:var(--sky)}
.footer-bar small{position:absolute;left:146px;top:24px;font-size:11.5px}
.social{position:absolute;top:18px;width:28px;height:28px;border:1px solid var(--white);border-radius:4px;display:flex;align-items:center;justify-content:center}
.social span{width:10px;height:10px;border-radius:50%;background:var(--white)}
</style>
</head>
<body>

<header class="site-header abs">
  <div class="brand abs"><span class="brand-dot"></span><span class="brand-name">Brisa Lagoon</span></div>
  <nav class="main-nav">
    <a href="#" class="active" style="left:506px">Home</a>
    <a href="#" style="left:601px">About Us</a>
    <a href="#" style="left:715px">Our Products</a>
    <a href="#" style="left:857px">Our Projects</a>
  </nav>
  <a class="nav-cta abs">Contact Us</a>
</header>

<div class="photo" role="img" aria-label="Glass-fenced pool with blue tiles and a line of pine trees at sunset" style="left:0;top:143px;width:1200px;height:574px;background:linear-gradient(180deg,#c9d9b4 0%,#8fa25a 35%,#3aa9d6 62%,#1c9ae0 100%)"></div>

<section class="hero-band abs">
  <h1 class="title">Transform Your Garden with<br>Our Premium Above-Ground Pools!</h1>
  <p>Achieve your dreams with our custom, tailor-made above-ground pools.</p>
  <a class="btn-outline" style="left:498px;top:226px;width:204px;height:60px">Contact us
    <svg class="arrow" viewBox="0 0 20 20"><circle cx="10" cy="10" r="10" fill="#fff"/><path d="M8 6l4 4-4 4" stroke="#00dde6" stroke-width="2" fill="none"/></svg></a>
</section>

<div class="photo" role="img" aria-label="Blue tiled pool with steel ladder, palms reflected in the water" style="left:0;top:1055px;width:606px;height:695px;background:linear-gradient(180deg,#6fae4c 0%,#2a58c8 30%,#1d4fd0 75%,#c47a6e 100%)"></div>

<section class="why-panel abs">
  <h2 class="title">Why Choose Our<br>Above-Ground Pools?</h2>
  <div class="rule" style="left:57px;top:232px"></div>
  <ul class="why-list">
    <li style="margin-bottom:20px"><svg viewBox="0 0 44 44" fill="none" stroke="#fff" stroke-width="2"><circle cx="22" cy="24" r="14"/><path d="M15 24l5 5 9-10"/><path d="M22 4v5M10 8l3 4M34 8l-3 4"/></svg><b>Superior Quality:</b> Each pool is constructed with high-quality materials, ensuring exceptional durability and strength.</li>
    <li style="margin-bottom:20px"><svg viewBox="0 0 44 44" fill="none" stroke="#fff" stroke-width="2"><path d="M8 15l6-7h16l6 7-14 20z"/><path d="M8 15h28M16 15l6 20 6-20"/></svg><b>Elegant Design:</b> Our pools come in a variety of styles and finishes, seamlessly blending into any garden setting.</li>
    <li style="margin-bottom:20px"><svg viewBox="0 0 44 44" fill="none" stroke="#fff" stroke-width="2"><circle cx="22" cy="22" r="15" stroke-dasharray="5 3"/><path d="M15 29l11-11M24 14l6 6"/></svg><b>Custom and Tailor-Made:</b> Create the pool of your dreams withour customization options, tailored to your specific tastes and needs.</li>
    <li style="margin-bottom:20px"><svg viewBox="0 0 44 44" fill="none" stroke="#fff" stroke-width="2.5"><circle cx="22" cy="22" r="16" stroke-dasharray="6 3"/><circle cx="22" cy="22" r="10"/><path d="M17 22l4 4 6-7"/></svg><b>Easy Installation:</b> Enjoy your new oasis quickly with our simple and fast installation process.</li>
    <li><svg viewBox="0 0 44 44" fill="none" stroke="#fff" stroke-width="2"><circle cx="22" cy="20" r="11"/><path d="M17 20l4 4 6-7M18 33h8M19 38h6M22 3v4M8 10l3 3M36 10l-3 3"/></svg><b>Constant Innovation:</b> We incorporate the latest technologies to provide you with an optimal and safe swimming experience.</li>
  </ul>
</section>

<section class="service-panel abs">
  <h2 class="title">Personalized<br>Services</h2>
  <div class="rule" style="left:76px;top:198px"></div>
  <p class="copy">We understand that every garden and client is unique. That's why we offer personalized services, from design to installation and after-sales support. Our team of experts is here to answer all your questions and guide you throughout your project</p>
  <a class="btn-outline" style="left:75px;top:413px;width:204px;height:60px">Contact us
    <svg class="arrow" viewBox="0 0 20 20"><circle cx="10" cy="10" r="10" fill="#fff"/><path d="M8 6l4 4-4 4" stroke="#4fcfd9" stroke-width="2" fill="none"/></svg></a>
</section>

<div class="photo" role="img" aria-label="Resort pool in emerald water surrounded by palm trees and parasols" style="left:465px;top:1759px;width:735px;height:536px;background:linear-gradient(180deg,#7fa86a 0%,#3d7a4e 40%,#16a09a 70%,#0d7f7d 100%)"></div>

<section class="products abs">
  <h2 class="title">Our Products</h2>
  <div class="rule" style="left:562px;top:189px"></div>
  <article class="product-card" style="left:76px">
    <div class="pic" role="img" aria-label="Aluminium pool beside a glass building" style="background:linear-gradient(180deg,#d8e2e6 0%,#9fb4bd 55%,#28c0e8 100%)"></div>
    <div class="label">Aluminium Pools</div>
  </article>
  <article class="product-card featured" style="left:344px">
    <h3>Above-Ground Pools<br>with Aluminium &amp;Wood</h3>
    <div class="mini-rule"></div>
    <p>Enhance your outdoor space with our stylish and durable above-ground pools, combining the sleekness of aluminium with the natural beauty of wood.</p>
    <a class="btn-outline">Know More
      <svg class="arrow" viewBox="0 0 20 20" style="width:14px;height:14px"><circle cx="10" cy="10" r="10" fill="#fff"/><path d="M8 6l4 4-4 4" stroke="#28c0e8" stroke-width="2" fill="none"/></svg></a>
  </article>
  <article class="product-card" style="left:610px">
    <div class="pic" role="img" aria-label="Clear pool with composite wood decking" style="background:linear-gradient(180deg,#54c6e2 0%,#7fd6ea 55%,#a08067 100%)"></div>
    <div class="label">Galvanized Steel Pools with CompositeWood Coverings</div>
  </article>
  <article class="product-card" style="left:875px">
    <div class="pic" role="img" aria-label="Mini pool spa with lounge chairs by the sea" style="background:linear-gradient(180deg,#cfe3d4 0%,#5f8f6b 45%,#5a5060 100%)"></div>
    <div class="label">Mini Pool Spa</div>
  </article>
</section>

<section class="satisfaction abs" role="img" aria-label="Aerial view of a curved blue pool on a stone deck">
  <h2 class="title">Guaranteed Satisfaction</h2>
  <div class="rule" style="left:562px;top:187px"></div>
  <p class="copy">Your satisfaction is our top priority. We are committed to providing you with exceptional service and the highest quality products.<br>Join our community of satisfied customers who are already enjoying their custom above-ground pools.</p>
  <p class="warranty">10-Year Warranty!</p>
</section>

<div class="photo" role="img" aria-label="Aerial view of a rectangular pool with loungers and flowering shrubs" style="left:0;top:3487px;width:651px;height:479px;background:radial-gradient(ellipse at 45% 50%,#3fc6cf 0%,#1f8a94 45%,#1f5f6e 100%)"></div>

<section class="contact-panel abs">
  <h2 class="title">Contact Us Today</h2>
  <div class="rule" style="left:41px;top:128px"></div>
  <p class="copy">Don't wait any longer to transform your garden into a wellness oasis. Contact us today to discover our range of customizable above-ground pools and get a tailored quote. Dive into a world of infinite possibilities with Brisa Lagoon</p>
  <a class="btn-outline" style="left:45px;top:335px;width:204px;height:61px">Contact us
    <svg class="arrow" viewBox="0 0 20 20"><circle cx="10" cy="10" r="10" fill="#fff"/><path d="M8 6l4 4-4 4" stroke="#4fcfd9" stroke-width="2" fill="none"/></svg></a>
</section>

<footer class="site-footer abs">
  <div class="footer-item" style="left:199px">
    <svg viewBox="0 0 30 30" fill="none" stroke="#fff" stroke-width="1.5"><rect x="1" y="1" width="28" height="28" rx="4"/><path d="M10 9c0 7 4 11 11 11l1-3-3-1-1 1c-2-1-3-2-4-4l1-1-1-3z"/></svg>
    <div>CALL US<br>+41 21 555 0142</div>
  </div>
  <div class="footer-item" style="left:430px">
    <svg viewBox="0 0 30 30" fill="none" stroke="#fff" stroke-width="1.5"><rect x="1" y="1" width="28" height="28" rx="4"/><rect x="8" y="10" width="14" height="10"/><path d="M8 10l7 6 7-6"/></svg>
    <div>EMAIL US<br>hello@brisalagoon.ch</div>
  </div>
  <div class="footer-item" style="left:736px">
    <svg viewBox="0 0 30 30" fill="none" stroke="#fff" stroke-width="1.5"><rect x="1" y="1" width="28" height="28" rx="4"/><path d="M15 23s-6-6-6-10a6 6 0 0112 0c0 4-6 10-6 10z"/><circle cx="15" cy="13" r="2"/></svg>
    <div>Address line Dummy Here<br>Address line Here</div>
  </div>
  <div class="footer-rule"></div>
  <nav class="footer-nav">
    <a href="#" class="active" style="left:318px">HOME</a>
    <a href="#" style="left:390px">ABOUT US</a>
    <a href="#" style="left:523px">OUR PRODUCTS</a>
    <a href="#" style="left:658px">OUR SERVICES</a>
    <a href="#" style="left:783px">CONTACT US</a>
  </nav>
</footer>

<div class="footer-bar abs">
  <small>Copyright © 2024 All Rights Reserved By Brisa Lagoon</small>
  <a class="social" style="left:910px"><span></span></a>
  <a class="social" style="left:945px"><span></span></a>
  <a class="social" style="left:980px"><span></span></a>
  <a class="social" style="left:1015px"><span></span></a>
</div>

</body>
</html>
```